HearthMile business card and stationary design

We are looking for a simple yet elegant design for our mortgage company business card and stationary.

The card should include:
Name (Marcus Pell)
Title (CEO)
Phone Number (732-555-0182)
Address (48 Birchwell Court, Suite 314, Larkston, NJ 08841)
Email (email@hearthmile.example)
"NMLS" i.e. (NMLS 61947)
"Company NMLS" (Company NMLS 274615)

Contact Information for Business Card

See above

```html
<!DOCTYPE html>
<html lang="en">
<head>
<meta charset="utf-8">
<title>HearthMile Business Card</title>
<link rel="stylesheet" href="https://fonts.googleapis.com/css2?family=Montserrat:wght@500;700&family=Arimo:wght@400;700&display=swap">
<style>
  :root {
    --brand-blue: #03aeee;
    --ink-dark: #1b2431;
    --ink-body: #1e1e1e;
    --card-white: #ffffff;
    --backdrop: #2b2b2b;
    --back-mark: #0d3a55;
  }
  * { box-sizing: border-box; margin: 0; padding: 0; }
  html, body {
    width: 1093px; height: 1200px; overflow: hidden;
    background: var(--backdrop);
  }
  .canvas { position: relative; width: 1093px; height: 1200px; }
  .card {
    position: absolute; left: 264px; width: 580px; height: 357px;
    box-shadow: 2px 3px 6px rgba(0,0,0,.5);
  }
  .card--front { top: 226px; background: var(--card-white); }
  .card--back { top: 620px; background: var(--brand-blue); }

  .wordmark {
    position: absolute;
    font-family: "Montserrat", sans-serif; font-weight: 500;
    white-space: nowrap; line-height: 1;
  }
  .card--front .wordmark {
    right: 40px; top: 74px; font-size: 44px; color: var(--brand-blue);
  }
  .card--back .wordmark {
    left: 34px; right: 0; text-align: center; top: 166px;
    font-size: 55px; color: var(--back-mark);
  }

  .person { position: absolute; left: 33px; top: 162px; }
  .person__name {
    font-family: "Montserrat", sans-serif; font-weight: 700;
    font-size: 25px; color: var(--ink-dark); line-height: 1;
  }
  .person__name .surname { color: var(--brand-blue); }
  .person__title {
    font-family: "Arimo", sans-serif; font-size: 16px;
    color: var(--ink-body); margin-top: 5px;
  }

  .rule {
    position: absolute; left: 34px; width: 508px; height: 1px;
    background: var(--brand-blue);
  }
  .rule--top { top: 220px; }
  .rule--bottom { top: 308px; }

  .details {
    position: absolute; font-family: "Arimo", sans-serif;
    font-size: 16px; line-height: 21px; color: var(--ink-body);
  }
  .details--contact { left: 33px; top: 232px; }
  .details--license { left: 348px; top: 253px; }
  .label { color: var(--brand-blue); font-weight: 700; }
  .label--plain { color: var(--brand-blue); }
  .accent { color: var(--brand-blue); }

  .address {
    position: absolute; left: 0; right: 0; top: 320px;
    font-family: "Arimo", sans-serif; font-size: 16px;
    color: var(--ink-body); text-align: center;
    display: flex; justify-content: center; align-items: center; gap: 4px;
  }
  .address svg { width: 12px; height: 17px; }
</style>
</head>
<body>
<main class="canvas">
  <section class="card card--front" aria-label="Business card front">
    <div class="wordmark">HearthMile</div>

    <div class="person">
      <div class="person__name">Marcus <span class="surname">Pell</span></div>
      <div class="person__title">CEO</div>
    </div>

    <div class="rule rule--top"></div>

    <div class="details details--contact">
      <div><span class="label">T:</span> 732-555-0182</div>
      <div><span class="label">E:</span> email@hearthmile.example</div>
      <div><span class="label">W:</span> www.<span class="accent">hearthmile</span>.com</div>
    </div>

    <div class="details details--license">
      <div><span class="label--plain">NMLS</span> 61947</div>
      <div><span class="label--plain">Company NMLS</span> 274615</div>
    </div>

    <div class="rule rule--bottom"></div>

    <div class="address">
      <svg viewBox="0 0 12 17" aria-hidden="true">
        <path d="M6 0C2.7 0 0 2.6 0 5.9 0 10 6 17 6 17s6-7 6-11.1C12 2.6 9.3 0 6 0zm0 8.3a2.4 2.4 0 1 1 0-4.8 2.4 2.4 0 0 1 0 4.8z" fill="var(--brand-blue)"/>
      </svg>
      <span>48 Birchwell Court, Suite 314, Larkston, NJ 08841</span>
    </div>
  </section>

  <section class="card card--back" aria-label="Business card back">
    <div class="wordmark">HearthMile</div>
  </section>
</main>
</body>
</html>
```